Brindle Asset Management Vendor Recruiting Email

We need a digital flyer to email and post on Social media to attract new vendors to our website to apply to complete maintenance work on our clients homes. I have one flyer we had produced recently that we are un-happy with. It is attached.

The example given is what we do not want!! We do not want any of the pictures used from the existing one

Target Market(s)

Construction companies and handyman

Industry/Entity Type

Residential maintenance and repairs

Requirements
Must have
• Join our team as the header not become a vendor

```html
<!DOCTYPE html>
<html lang="en">
<head>
<meta charset="UTF-8">
<title>Brindle Asset Management – Join Our Team</title>
<link rel="stylesheet" href="https://fonts.googleapis.com/css2?family=Pinyon+Script&family=Montserrat:wght@900&family=Oswald:wght@600;700&family=Figtree:wght@500;600&family=Open+Sans:ital,wght@1,600&display=swap">
<style>
  :root{
    --plum:#674d7c;
    --ink:#0a0a0a;
    --white:#ffffff;
    --outline:#231a2b;
    --lime:#d6e021;
    --lime-dot:#d9e22a;
    --blue:#1b75bb;
    --violet-text:#5b2a86;
    --lavender:#8a88c0;
    --logo-box:#0d0c18;
  }
  *{margin:0;padding:0;box-sizing:border-box;}
  html,body{width:1200px;height:1200px;overflow:hidden;background:#ffffff;}
  .flyer{position:absolute;left:0;top:62px;width:1200px;height:1075px;background:var(--plum);overflow:hidden;}
  .frame{position:absolute;left:34px;top:21px;width:1132px;height:1033px;border:2px solid var(--white);border-radius:26px;overflow:hidden;}

  .headline-script{position:absolute;left:20px;right:0;top:24px;text-align:center;font-family:"Pinyon Script",cursive;font-size:134px;line-height:1;color:var(--white);-webkit-text-stroke:1.2px var(--outline);paint-order:stroke fill;white-space:nowrap;}
  .headline-today{position:absolute;left:40px;right:0;top:138px;text-align:center;font-family:"Montserrat",sans-serif;font-weight:900;font-size:136px;line-height:1;color:var(--ink);letter-spacing:-6px;white-space:nowrap;}

  .divider{position:absolute;left:546px;top:288px;width:2px;height:456px;background:var(--white);}

  .benefits,.requirements ul{list-style:none;}
  .benefits li,.requirements li{position:relative;font-family:"Figtree",sans-serif;font-weight:600;color:var(--white);white-space:nowrap;}
  .benefits li::before,.requirements li::before{content:"";position:absolute;left:0;width:11px;height:11px;border-radius:50%;background:var(--lime-dot);}

  .benefits{position:absolute;left:34px;top:311px;}
  .benefits li{font-size:27px;line-height:34.6px;letter-spacing:.8px;padding-left:30px;margin-bottom:34.6px;}
  .benefits li::before{top:11px;}

  .requirements{position:absolute;left:579px;top:282px;}
  .requirements h2{font-family:"Oswald",sans-serif;font-weight:700;font-size:40px;line-height:51px;color:var(--lime);text-transform:uppercase;letter-spacing:.3px;margin-bottom:11px;}
  .requirements li{font-size:25px;line-height:29.5px;letter-spacing:.7px;padding-left:32px;margin-bottom:25.5px;}
  .requirements li::before{top:10px;left:6px;}

  .contact{position:absolute;left:123px;top:817px;transform:rotate(-3deg);transform-origin:left top;}
  .contact-tab{position:absolute;left:97px;top:-34px;width:150px;height:40px;background:var(--white);border-radius:4px 4px 0 0;font-family:"Oswald",sans-serif;font-weight:700;font-size:24px;color:var(--violet-text);text-align:center;line-height:40px;}
  .contact-phone{position:relative;width:508px;height:118px;background:var(--blue);border:3px solid var(--white);border-radius:8px;box-shadow:2px 3px 4px rgba(0,0,0,.35);font-family:"Oswald",sans-serif;font-weight:700;font-size:80px;line-height:110px;color:var(--white);text-align:center;letter-spacing:3px;}

  .footer-bar{position:absolute;left:0;top:951px;width:100%;height:59px;background:var(--ink);}
  .footer-band{position:absolute;left:0;top:1010px;width:100%;height:23px;background:var(--lavender);}
  .website{position:absolute;left:132px;top:960px;display:flex;align-items:center;gap:9px;font-family:"Open Sans",sans-serif;font-style:italic;font-weight:600;font-size:30px;line-height:41px;color:var(--white);}

  .brand-box{position:absolute;left:755px;top:855px;width:274px;height:155px;background:var(--logo-box);display:flex;align-items:flex-end;justify-content:center;text-align:center;padding-bottom:24px;}
  .brand-name{font-family:"Figtree",sans-serif;font-weight:600;font-size:22px;line-height:27px;color:var(--white);}
</style>
</head>
<body>
<div class="flyer">
  <div class="frame">
    <h1>
      <span class="headline-script">Join Our Team</span>
      <span class="headline-today">TODAY!</span>
    </h1>

    <ul class="benefits">
      <li>95% approval rating on all<br>submitted estimates.</li>
      <li>Guaranteed work volume.</li>
      <li>Material purchasing program to<br>help vendors with low capital or no<br>or bad credit.</li>
      <li>Weekly secure direct deposit with<br>net 30 payment terms.</li>
    </ul>

    <div class="divider"></div>

    <section class="requirements">
      <h2>Requirements to become a<br>vendor</h2>
      <ul>
        <li>Auto insurance</li>
        <li>Certificate of general liability insurance</li>
        <li>Workman’s Compensation or state issued<br>exemption letter</li>
        <li>Drive License or state issued ID card</li>
        <li>Coverage area</li>
        <li>Any speciality Licenses</li>
      </ul>
    </section>

    <div class="contact">
      <div class="contact-tab">CONTACT</div>
      <div class="contact-phone">555-204-3178</div>
    </div>

    <div class="footer-bar"></div>
    <div class="footer-band"></div>
    <div class="website">
      <svg width="30" height="30" viewBox="0 0 30 30" fill="none" stroke="#ffffff" stroke-width="2" aria-hidden="true">
        <circle cx="15" cy="15" r="13"/>
        <ellipse cx="15" cy="15" rx="6" ry="13"/>
        <line x1="2" y1="15" x2="28" y2="15"/>
      </svg>
      <span>www.brindleassetgroup.com</span>
    </div>

    <div class="brand-box">
      <p class="brand-name">Brindle<br>Asset Management</p>
    </div>
  </div>
</div>
</body>
</html>
```